Geschäftspapiere für Fliesenleger - Meisterbetrieb
Zielgruppe
Wir sind ein mittelständischer Fliesenleger - Meisterbetrieb und möchten unsere Geschäftspapiere erneuern. Unsere Kunden sind Privatkunden, Gewerbetreibende sowie Öffentliche Auftraggeber.
Aufgabenstellung
Unser Logo stellen wir Ihnen zur verfügung und soll unverändert bleiben.
Wir benötigen folgende Geschäftspapiere:
- Briefpapier DIN A4
- Notizblock Karriert DIN A4
- Visitenkarten 5,5 x 8,5 cm
- Kuvert DIN lang mit Fenster
- Kuvert DIN C4 mit Fenster
Bei der Farbe Rot handelt es sich um Verkehrsrot RAL 3020
Als Schriftart haben wir uns Helvetica Neue vorgestellt.
Wir bitten jedoch auch um Vorschläge anderer Moderner und gut lesbarer Schriftarten die für Print und Web bestens geeignet sind.
Wir wünschen uns ein Modernes und Schnörkelloses Design. Bei den Dateien habe ich Ihnen ein Stockphoto angehängt um Ihnen zu zeigen wie wir uns ein Cover oder eine Broschüre vorstellen können. Nur um Ihnen unsere Ideen / Vorstellungen näher zu bringen.

```html
<!DOCTYPE html>
<html lang="de">
<head>
<meta charset="utf-8">
<title>Fliesen-Kramm – Geschäftsausstattung</title>
<link rel="stylesheet" href="https://fonts.googleapis.com/css2?family=Arimo:wght@400;700&display=swap">
<style>
  :root {
    --paper: #ffffff;
    --stage: #ffffff;
    --ink: #1d1d1b;
    --traffic-red: #e2141f;
    --window-grey: #c3c2c0;
    --mid-grey: #8a8a8a;
    --light-grey: #cfcfcf;
  }
  * { box-sizing: border-box; margin: 0; padding: 0; }
  html, body {
    width: 1071px; height: 1200px; overflow: hidden;
    background: var(--stage);
    font-family: "Arimo", "Helvetica Neue", Arial, sans-serif;
    color: var(--ink);
  }
  .stationery { position: relative; width: 1071px; height: 1200px; }

  .sheet {
    position: absolute;
    background: var(--paper);
    box-shadow: 0 6px 14px rgba(0,0,0,0.16), 0 1px 3px rgba(0,0,0,0.08);
    overflow: hidden;
  }
  .envelope-dl { width: 352px; height: 165px; top: 240px; }
  .envelope-c4 { width: 352px; height: 498px; top: 446px; }
  .variant-band { left: 173px; }
  .variant-tiles { left: 558px; }

  .wordmark {
    position: absolute;
    font-weight: 700;
    font-size: 13px;
    line-height: 1;
    color: var(--ink);
    white-space: nowrap;
    display: flex; align-items: center; gap: 4px;
  }
  .wordmark::before {
    content: ""; width: 6px; height: 6px; background: var(--traffic-red);
  }
  .envelope-dl .wordmark { left: 22px; top: 36px; }

  .address-window {
    position: absolute;
    background: var(--window-grey);
    border-radius: 7px;
    width: 157px;
  }
  .envelope-dl .address-window { left: 31px; top: 67px; height: 62px; }
  .envelope-c4 .address-window { left: 33px; top: 78px; height: 87px; }

  .footer-band { position: absolute; left: 0; width: 100%; }
  .footer-band .red { height: 6px; background: var(--traffic-red); margin-right: 125px; }
  .footer-band .black { height: 7px; background: var(--ink); }
  .footer-band .tile-strip {
    position: absolute; top: 0; right: 0; width: 125px; height: 6px;
    background: linear-gradient(90deg, var(--mid-grey), var(--ink) 40%, var(--traffic-red) 75%, var(--light-grey));
  }
  .envelope-dl .footer-band { top: 152px; }
  .envelope-c4 .footer-band { top: 478px; }

  .tile-pattern {
    position: absolute;
    width: 137px; height: 49px;
    background: linear-gradient(90deg, #4a4a4a 0%, #e2141f 45%, #8a8a8a 75%, #1d1d1b 100%);
    opacity: 0.85;
  }
  .envelope-dl .tile-pattern { left: 215px; top: 71px; }
  .envelope-c4 .tile-pattern.top { left: 215px; top: 27px; }
  .envelope-c4 .tile-pattern.bottom { left: 0; top: 428px; }

  .envelope-c4 .sender-block {
    position: absolute; right: 28px; text-align: right;
  }
  .envelope-c4 .sender-block .wordmark { position: static; justify-content: flex-end; }
  .variant-band .sender-block { top: 425px; }
  .variant-tiles .sender-block { top: 460px; }
  .web-address {
    margin-top: 18px;
    font-size: 8.7px;
    color: var(--ink);
  }
</style>
</head>
<body>
<main class="stationery">

  <section class="sheet envelope-dl variant-band">
    <div class="wordmark">Fliesen-Kramm</div>
    <div class="address-window"></div>
    <div class="footer-band">
      <div class="red"></div><div class="black"></div>
      <div class="tile-strip" role="img" aria-label="Schmale Zierleiste in Grau, Schwarz und Rot"></div>
    </div>
  </section>

  <section class="sheet envelope-dl variant-tiles">
    <div class="wordmark">Fliesen-Kramm</div>
    <div class="address-window"></div>
    <div class="tile-pattern" role="img" aria-label="Muster aus liegenden Fliesenstreifen in Rot, Grau und Schwarz"></div>
  </section>

  <section class="sheet envelope-c4 variant-band">
    <div class="address-window"></div>
    <div class="sender-block">
      <div class="wordmark">Fliesen-Kramm</div>
      <p class="web-address">www.fliesen-kramm.de</p>
    </div>
    <div class="footer-band">
      <div class="red"></div><div class="black"></div>
      <div class="tile-strip" role="img" aria-label="Schmale Zierleiste in Grau, Schwarz und Rot"></div>
    </div>
  </section>

  <section class="sheet envelope-c4 variant-tiles">
    <div class="tile-pattern top" role="img" aria-label="Muster aus liegenden Fliesenstreifen in Rot, Grau und Schwarz"></div>
    <div class="address-window"></div>
    <div class="tile-pattern bottom" role="img" aria-label="Muster aus liegenden Fliesenstreifen in Rot, Grau und Schwarz"></div>
    <div class="sender-block">
      <div class="wordmark">Fliesen-Kramm</div>
    </div>
  </section>

</main>
</body>
</html>
```